KBT Business Cards

We require business cards for our business. We would like a matte black back to the card, with our logo centred in the middle. The front side of the card is open to design.

Target Market(s)

Clients looking for legal services (professional)

Industry/Entity Type

Legal

Contact Information for Business Card

Doran Kelbrath
Partner
Mobile: 0461 738 524
Email: doran@kbtlaw.co
Website: www.kbtlaw.co
Level 3, 118 Wendmore Street
Sydney NSW 2000

Font styles to use
Other font styles liked:
• Avenir

Colors
f04a50
ffffff
1b1b1b

Requirements
Must have
• Black back with logo included in the centre of the card.
• Our font is Avenir.

```html
<!DOCTYPE html>
<html lang="en">
<head>
<meta charset="utf-8">
<title>KBT Business Cards</title>
<link href="https://fonts.googleapis.com/css2?family=Roboto:wght@400;500;700&display=swap" rel="stylesheet">
<style>
  :root {
    --stage: #7b7b7b;
    --paper: #ffffff;
    --ink: #1b1b1b;
    --crimson: #c8183f;
    --matte-black: #1b1b1b;
    --rule: #2a2a2a;
  }
  * { margin: 0; padding: 0; box-sizing: border-box; }
  html, body { width: 1200px; height: 1200px; overflow: hidden; }
  body {
    background: var(--stage);
    font-family: "Roboto", Arial, sans-serif;
    position: relative;
  }
  .card {
    position: absolute;
    top: 310px;
    height: 594px;
    box-shadow: 3px 4px 6px rgba(0,0,0,0.45);
    overflow: hidden;
  }
  .card-front { left: 234px; width: 364px; background: var(--paper); }
  .card-back { left: 627px; width: 369px; background: var(--matte-black); }

  .brand {
    position: absolute;
    left: 66px;
    top: 152px;
    display: flex;
    align-items: center;
    gap: 67px;
  }
  .brand-mark { width: 46px; height: 46px; background: var(--crimson); flex: none; }
  .brand-name {
    color: var(--ink);
    font-weight: 500;
    font-size: 26px;
    line-height: 28px;
    letter-spacing: 0.2px;
  }

  .contact {
    position: absolute;
    left: 0; right: 0;
    top: 356px;
    text-align: center;
    color: var(--ink);
    font-size: 17px;
    line-height: 21.5px;
  }
  .person-name { color: var(--crimson); font-weight: 700; font-size: 21px; line-height: 24px; }
  .person-role { font-size: 17px; line-height: 18px; }
  .divider { width: 150px; height: 1px; background: var(--rule); margin: 10px auto 9px; }
  .label { color: var(--crimson); font-weight: 500; }
  .web { font-weight: 700; color: var(--crimson); }

  .back-brand {
    position: absolute;
    left: 0; right: 0;
    top: 0; bottom: 0;
    display: flex;
    flex-direction: column;
    align-items: center;
    justify-content: center;
    gap: 22px;
  }
  .back-mark { width: 40px; height: 40px; background: var(--crimson); }
  .back-name {
    text-align: center;
    color: var(--paper);
    font-weight: 500;
    font-size: 28px;
    line-height: 32px;
    letter-spacing: 1px;
  }
  .back-web {
    position: absolute;
    left: 0; right: 0;
    top: 530px;
    text-align: center;
    color: var(--crimson);
    font-weight: 700;
    font-size: 17px;
  }
</style>
</head>
<body>
  <section class="card card-front">
    <div class="brand">
      <span class="brand-mark"></span>
      <div class="brand-name">KELBRATH<br>BRYCE<br>TANNER</div>
    </div>
    <div class="contact">
      <p class="person-name">DORAN KELBRATH</p>
      <p class="person-role">Partner</p>
      <div class="divider"></div>
      <p><span class="label">M:</span> 0461 738 524</p>
      <p><span class="label">E:</span> doran@kbtlaw.co</p>
      <p class="web">www.kbtlaw.co</p>
      <div class="divider"></div>
      <p>Level 3, 118 Wendmore<br>Street, Sydney NSW 2000</p>
    </div>
  </section>

  <section class="card card-back">
    <div class="back-brand">
      <span class="back-mark"></span>
      <p class="back-name">KELBRATH<br>BRYCE<br>TANNER</p>
    </div>
    <p class="back-web">www.kbtlaw.co</p>
  </section>
</body>
</html>
```